business card deign

Logo needs the following on it.
1. attached logo
2. Tagline - "If it keeps a drink cold or the party going...we do it!"
3. Name- Dalton Pikes, Founder and CPO
4. Address - 412 E. Carver Avenue, Ste 2207, Tampa, FL. 33917
5. Phone - 555.318.4726

```html
<!DOCTYPE html>
<html lang="en">
<head>
<meta charset="utf-8">
<title>Frostly Business Card</title>
<link rel="stylesheet" href="https://fonts.googleapis.com/css2?family=Montserrat:wght@400;700&display=swap">
<style>
  :root {
    --bg: #9a9a9a;
    --card-light: #ffffff;
    --card-dark: #2a2a2a;
    --ink: #2b2b2b;
    --ink-soft: #3a3a3a;
    --paper: #ffffff;
  }
  * { margin: 0; padding: 0; box-sizing: border-box; }
  html, body { width: 1200px; height: 1059px; overflow: hidden; }
  body {
    background: var(--bg);
    font-family: "Montserrat", sans-serif;
    position: relative;
  }
  .card {
    position: absolute;
    width: 692px;
    height: 392px;
    border-radius: 22px;
  }
  .card--front { left: 256px; top: 89px; background: var(--card-light); color: var(--ink); }
  .card--back { left: 254px; top: 570px; background: var(--card-dark); color: var(--paper); }

  .brand-mark {
    position: absolute;
    border-radius: 50%;
  }
  .card--front .brand-mark { left: 170px; top: 122px; width: 70px; height: 70px; background: var(--ink); }
  .card--back .brand-mark { left: 303px; top: 96px; width: 88px; height: 88px; background: var(--paper); }

  .brand-name {
    position: absolute;
    font-family: "Montserrat", sans-serif;
    font-weight: 700;
    white-space: nowrap;
    text-align: center;
  }
  .card--front .brand-name { left: 80px; width: 250px; top: 212px; font-size: 28px; }
  .card--back .brand-name { left: 196px; width: 300px; top: 210px; font-size: 38px; }

  .divider {
    position: absolute;
    left: 339px; top: 117px;
    width: 1px; height: 162px;
    background: var(--ink);
  }
  .contact { position: absolute; left: 372px; top: 114px; }
  .contact__name { font-weight: 700; font-size: 24px; letter-spacing: 0.5px; line-height: 1; text-transform: uppercase; }
  .contact__title { font-size: 15.5px; margin-top: 5px; color: var(--ink-soft); }
  .contact__address { font-size: 16.5px; line-height: 23px; margin-top: 16px; color: var(--ink-soft); letter-spacing: 0.3px; }
  .contact__line { display: flex; align-items: center; gap: 7px; font-size: 16.5px; color: var(--ink-soft); margin-top: 8px; letter-spacing: 0.3px; }
  .contact__line:first-of-type { margin-top: 14px; }
  .contact__line svg { width: 11px; height: 11px; fill: var(--ink); flex: none; }

  .tagline {
    position: absolute;
    left: 0; right: 0; top: 339px;
    text-align: center;
    font-size: 15.5px;
    letter-spacing: 0.3px;
  }
</style>
</head>
<body>
  <section class="card card--front">
    <span class="brand-mark"></span>
    <div class="brand-name">Frostly</div>
    <span class="divider"></span>
    <div class="contact">
      <div class="contact__name">Dalton Pikes</div>
      <div class="contact__title">Founder and CPO</div>
      <div class="contact__address">412 E. Carver Avenue<br>Ste 2207, Tampa, FL. 33917</div>
      <div class="contact__line">
        <svg viewBox="0 0 12 12" aria-hidden="true"><path d="M1 4.5C1 3 2.5 2 6 2s5 1 5 2.5v1H8.5V4.3h-5v1.2H1z M3 6h6l1.5 4.5h-9z"/></svg>
        <span>555.318.4726</span>
      </div>
      <div class="contact__line">
        <svg viewBox="0 0 12 12" aria-hidden="true"><path d="M1 5l5-4 5 4v6H1z M2 5.5l4 3 4-3" stroke="#fff" stroke-width="0.8"/></svg>
        <span>daltonpikes@mailhub.com</span>
      </div>
    </div>
  </section>

  <section class="card card--back">
    <span class="brand-mark"></span>
    <div class="brand-name">Frostly</div>
    <p class="tagline">If it keeps a drink cold or the party going...we do it!</p>
  </section>
</body>
</html>
```